Business Card Design for Training Business

Clear Path Coaching is a new business that delivers training and other services with a focus on topics related to mental health and wellbeing, for example, Wellmind Response Course, Resilience etc. We have a strong focus on evidence-based psychology and neuroscience. I have a logo which I will upload with the brief, so please consider colours that work well with the logo.
Target Market(s)
Adults, workplaces (particularly government and not-for-profits)
Industry/Entity Type
Business
Contact Information for Business Card
Head Strong TrainingSamantha SellwoodDirector0438 770 850sam@headstrongtraining.com.auwww.clearpathcoaching.example.au

```html
<!DOCTYPE html>
<html lang="en">
<head>
<meta charset="utf-8">
<title>Clear Path Coaching — Business Card</title>
<link rel="stylesheet" href="https://fonts.googleapis.com/css2?family=Lato:wght@300;400&display=swap">
<style>
  :root {
    --backdrop: #e9ecee;
    --teal-light: #38b9c4;
    --teal-mid: #26a3b0;
    --teal-deep: #17838f;
    --accent: #3ab6c2;
    --ink: #6a6262;
    --ink-soft: #8a8282;
    --paper: #ffffff;
  }
  * { margin: 0; padding: 0; box-sizing: border-box; }
  html, body {
    width: 1200px;
    height: 900px;
    overflow: hidden;
    background: var(--backdrop);
    font-family: "Lato", Arial, sans-serif;
  }
  .card {
    position: absolute;
    left: 100px;
    top: 164px;
    width: 1000px;
    height: 572px;
    border-radius: 22px;
    overflow: hidden;
    box-shadow: 0 10px 30px rgba(0,0,0,0.18);
  }
  .card__pattern {
    position: absolute;
    inset: 0;
    background:
      linear-gradient(128deg, rgba(255,255,255,0.10) 0%, rgba(255,255,255,0) 45%),
      linear-gradient(160deg, var(--teal-light) 0%, var(--teal-mid) 50%, var(--teal-deep) 100%);
  }
  .identity {
    position: absolute;
    left: 272px;
    top: 0;
    width: 366px;
    height: 268px;
    background: var(--paper);
    border-radius: 0 0 22px 22px;
    text-align: center;
    padding-top: 30px;
    box-shadow: 0 3px 10px rgba(0,0,0,0.12);
  }
  .identity__mark {
    display: block;
    margin: 0 auto 14px;
  }
  .identity__name {
    font-weight: 300;
    font-size: 36px;
    letter-spacing: 4px;
    color: var(--ink);
    line-height: 1;
    text-transform: uppercase;
  }
  .identity__tagline {
    font-weight: 300;
    font-size: 15px;
    letter-spacing: 8px;
    color: var(--ink);
    text-transform: uppercase;
    margin-top: 6px;
  }
  .person {
    margin-top: 20px;
    font-size: 22px;
    font-weight: 300;
    text-transform: uppercase;
    line-height: 1;
  }
  .person__first { color: var(--accent); }
  .person__last { color: var(--ink); }
  .person__role {
    font-size: 16px;
    color: var(--ink);
    margin-top: 6px;
    font-weight: 400;
  }
  .contact-bar {
    position: absolute;
    left: 22px;
    right: 22px;
    bottom: 24px;
    height: 66px;
    background: var(--paper);
    border-radius: 4px;
    display: flex;
    align-items: center;
    justify-content: space-between;
    padding: 0 28px;
    box-shadow: 0 2px 8px rgba(0,0,0,0.12);
  }
  .contact-bar__item {
    display: flex;
    align-items: center;
    gap: 14px;
    font-size: 19px;
    color: var(--ink);
    font-weight: 400;
  }
  .contact-bar__icon { fill: var(--ink-soft); stroke: var(--ink-soft); }
</style>
</head>
<body>
  <div class="card">
    <div class="card__pattern" role="img" aria-label="Faceted low-poly teal background pattern"></div>

    <div class="identity">
      <svg class="identity__mark" width="70" height="70" viewBox="0 0 70 70" aria-hidden="true">
        <circle cx="35" cy="35" r="31" fill="none" stroke="var(--accent)" stroke-width="3"/>
      </svg>
      <div class="identity__name">Clear Path</div>
      <div class="identity__tagline">Coaching</div>
      <div class="person">
        <span class="person__first">Rebecca</span> <span class="person__last">Tanfield</span>
      </div>
      <div class="person__role">Director</div>
    </div>

    <div class="contact-bar">
      <div class="contact-bar__item">
        <svg class="contact-bar__icon" width="22" height="18" viewBox="0 0 22 18" aria-hidden="true">
          <path d="M2 6 Q11 0 20 6 L18 8 L15 6 L7 6 L4 8 Z" stroke="none"/>
          <rect x="5" y="8" width="12" height="9" rx="2" stroke="none"/>
        </svg>
        <span>0491 362 517</span>
      </div>
      <div class="contact-bar__item">
        <svg class="contact-bar__icon" width="22" height="16" viewBox="0 0 22 16" aria-hidden="true">
          <rect x="1" y="1" width="20" height="14" stroke="none"/>
          <path d="M1 1 L11 9 L21 1" fill="none" stroke="#fff" stroke-width="1.6"/>
        </svg>
        <span>bec@clearpathcoaching.example.au</span>
      </div>
      <div class="contact-bar__item">
        <svg class="contact-bar__icon" width="20" height="20" viewBox="0 0 20 20" aria-hidden="true">
          <g fill="none" stroke-width="2.4" transform="rotate(-45 10 10)">
            <rect x="1" y="6.5" width="9" height="7" rx="3.5"/>
            <rect x="10" y="6.5" width="9" height="7" rx="3.5"/>
          </g>
        </svg>
        <span>clearpathcoaching.example.au</span>
      </div>
    </div>
  </div>
</body>
</html>
```